Redesign and move to Wordpress for corvandel.com

Our website needs a redesign and at the same time we are moving it to Wordpress. Please help us with a new digital professional look and feel.

We are an Australian Software Engineering company specialising in advanced software development using in A.I., PLatform Engineering, Integration and Cloud. See the current corvandel.com for more information about us.

```html
<!DOCTYPE html>
<html lang="en">
<head>
<meta charset="utf-8">
<title>Corvandel – Reliable Smart Software Engineering</title>
<link href="https://fonts.googleapis.com/css2?family=Exo+2:wght@300;400;500;600&display=swap" rel="stylesheet">
<style>
:root{
  --bg:#050b1f;
  --bg-deep:#030817;
  --card:#0a1433;
  --card-edge:#16245a;
  --blue:#2f6fe0;
  --blue-bright:#1530e0;
  --teal:#3fbfb0;
  --accent:#3aa5f0;
  --text:#ffffff;
  --muted:#c9d2ea;
  --orange:#f0731e;
  --cyan:#1fc4f0;
}
*{margin:0;padding:0;box-sizing:border-box}
html,body{width:1200px;height:4016px;overflow:hidden}
body{background:var(--bg);color:var(--text);font-family:"Exo 2",sans-serif;position:relative}
.abs{position:absolute}
/* nav */
.brand{display:flex;align-items:center;gap:14px;font-size:34px;font-weight:300;letter-spacing:2px;color:var(--text)}
.brand-square{width:40px;height:40px;border:3px solid var(--text)}
.site-nav{left:527px;top:32px;display:flex;gap:26px;font-size:15px}
.site-nav a{color:var(--text);text-decoration:none}
.site-nav a.active{color:var(--accent)}
.search-btn{left:1007px;top:25px;width:40px;height:40px;border-radius:6px;background:#0f1f5a;display:flex;align-items:center;justify-content:center}
/* hero */
.hero-art{left:60px;top:120px;width:420px;height:380px;border-radius:50%;background:radial-gradient(circle,rgba(30,100,230,.55),rgba(10,30,90,.25) 50%,transparent 72%)}
.hero-beam{left:440px;top:325px;width:660px;height:3px;background:linear-gradient(90deg,transparent,rgba(60,150,255,.8),transparent)}
.hero-title{left:488px;top:250px;font-size:58px;font-weight:400;line-height:66px}
/* intro */
.card{background:var(--card);border:1px solid var(--card-edge);border-radius:22px;box-shadow:0 0 30px rgba(20,60,160,.25)}
.intro{left:135px;top:525px;width:929px;height:293px}
.intro p{position:absolute;left:58px;top:60px;width:560px;font-size:21px;line-height:25px;color:var(--text)}
.intro-mark{position:absolute;left:690px;top:118px;display:flex;align-items:center;gap:14px;font-size:34px;color:var(--teal)}
.intro-mark span.sq{width:46px;height:46px;background:var(--blue)}
/* clients */
.clients{left:135px;top:895px;width:929px;display:flex;justify-content:space-around;align-items:center;font-size:34px;font-weight:600;color:#c6c9d4}
.clients .teal{color:var(--teal)}
/* services */
.services-band{left:0;top:1060px;width:1200px;height:620px;background:radial-gradient(ellipse at 50% 30%,rgba(30,70,170,.35),transparent 65%)}
.section-title{width:1200px;left:0;text-align:center;font-size:56px;font-weight:400}
.section-title .b{color:var(--blue)} .section-title .t{color:var(--teal)}
.svc{width:215px;height:397px;border-radius:108px;background:linear-gradient(#0c1744,#0a1540 70%,#1b2c78);border:1px solid var(--card-edge);text-align:center;padding:0 16px}
.svc.on{background:linear-gradient(#1a28d8,#1120b8 60%,#3b4fc8)}
.svc svg{margin-top:48px}
.svc h3{font-size:19px;font-weight:400;line-height:22px;margin-top:14px}
.svc hr{width:36px;border:0;border-top:1px solid var(--accent);margin:16px auto}
.svc p{font-size:12.5px;line-height:15.5px;color:var(--muted)}
.plus{left:450px;top:1592px;width:44px;height:44px;border-radius:50%;background:#071030;display:flex;align-items:center;justify-content:center;font-size:24px}
.divider{left:125px;top:1722px;width:950px;height:1px;background:#16245a}
.divider i{position:absolute;left:352px;top:-1px;width:244px;height:3px;background:var(--blue)}
/* news */
.news-lines{left:0;top:1770px;width:1200px;height:240px;background:radial-gradient(ellipse at 12% 50%,rgba(40,110,200,.25),transparent 30%),radial-gradient(ellipse at 88% 50%,rgba(40,110,200,.25),transparent 30%)}
.subtitle{left:0;width:1200px;text-align:center;font-size:22px}
.post{left:135px;width:929px;height:223px}
.post h4{position:absolute;font-size:29px;font-weight:400}
.post .lede{position:absolute;font-size:16px;color:var(--teal)}
.post .ex{position:absolute;font-size:12.5px;line-height:19px;color:var(--muted);width:500px}
.thumb{position:absolute;width:327px;height:171px;top:26px}
.thumb-label{position:absolute;inset:0;display:flex;align-items:center;justify-content:center;font-size:22px;font-weight:600;text-align:center;line-height:26px}
.scroll-track{left:1097px;top:2000px;width:2px;height:990px;background:#0c1744}
.scroll-track i{position:absolute;top:355px;width:2px;height:240px;background:var(--blue)}
/* newsletter */
.news-band{left:0;top:3061px;width:1200px;height:370px;background:radial-gradient(ellipse at 50% 50%,#10226a,#0a1648 60%,#071035)}
.promo{left:0;top:3128px;width:1200px;text-align:center;font-size:47px;line-height:56px;color:var(--blue)}
.promo .t{color:var(--teal)}
.signup{left:249px;top:3337px;width:686px;height:48px;border-radius:24px;background:#0a1540;border:1px solid #1f3070;overflow:hidden;display:flex}
.signup .field{flex:1;display:flex;align-items:center;gap:10px;padding-left:26px;font-size:13px;color:var(--muted)}
.signup .go{width:164px;background:var(--teal);display:flex;align-items:center;justify-content:center;font-size:18px;font-weight:600}
.consult{left:187px;top:3456px;width:826px;height:241px;text-align:center;padding-top:80px;font-size:35px;line-height:42px}
.consult .o{color:var(--orange);text-decoration:underline}
.consult .c{color:var(--cyan)} .consult .b{color:var(--blue)}
/* footer */
.footer-nav{left:0;width:1200px;top:3846px;display:flex;justify-content:center;gap:34px;font-size:15px}
.footer-nav a{color:var(--text);text-decoration:none}
.footer-nav a.active{color:var(--accent)}
.social{width:66px;height:66px;border-radius:50%;border:2px solid #1d2c72;background:#0a1540;display:flex;align-items:center;justify-content:center;font-size:17px;font-weight:600;color:var(--teal)}
.version{left:1040px;top:3928px;font-size:13px;color:var(--muted)}
</style>
</head>
<body>

<header>
  <div class="abs brand" style="left:137px;top:20px"><span class="brand-square"></span>corvandel</div>
  <nav class="abs site-nav"><a class="active" href="#">Home</a><a href="#">About Us</a><a href="#">Services</a><a href="#">Blog</a><a href="#">Contact Us</a></nav>
  <div class="abs search-btn"><svg width="16" height="16" viewBox="0 0 16 16"><circle cx="7" cy="7" r="4.5" fill="none" stroke="#fff" stroke-width="2"/><line x1="10.5" y1="10.5" x2="14" y2="14" stroke="#fff" stroke-width="2"/></svg></div>
</header>

<section class="hero">
  <div class="abs hero-art" role="img" aria-label="Glowing blue circuit board traces radiating from a central chip"></div>
  <div class="abs hero-beam"></div>
  <h1 class="abs hero-title">Reliable Smart<br>Software Engineering</h1>
</section>

<section class="abs card intro">
  <p>At Corvandel, we craft bespoke software solutions that are not available on the market. By building organizations market-leading products, process automation, legacy system enablement, or advanced intelligent systems, we empower our customers to achieve a competitive edge in their industry.</p>
  <div class="intro-mark"><span class="sq"></span>corvandel</div>
</section>

<div class="abs clients"><span>Norwell</span><span class="teal">Brightlane</span><span>Haulmark</span><span>Solvest</span></div>

<div class="abs services-band" role="img" aria-label="Flowing blue particle wave backdrop"></div>
<h2 class="abs section-title" style="top:1085px"><span class="b">Our</span> <span class="t">Services</span></h2>

<article class="abs svc" style="left:137px;top:1200px">
  <svg width="90" height="90" viewBox="0 0 90 90" fill="none" stroke="#3fbfb0" stroke-width="2.5"><circle cx="34" cy="34" r="14"/><circle cx="34" cy="34" r="5"/><circle cx="60" cy="60" r="12"/><circle cx="60" cy="60" r="4"/></svg>
  <h3>Enterprise Systems Integration</h3><hr>
  <p>Automate your business processes internally or externally to improve data quality and process efficiency</p>
</article>
<article class="abs svc on" style="left:377px;top:1246px">
  <svg width="90" height="90" viewBox="0 0 90 90" fill="none" stroke="#fff" stroke-width="2.5"><circle cx="45" cy="45" r="16"/><circle cx="45" cy="45" r="7"/><circle cx="12" cy="12" r="5"/><circle cx="78" cy="12" r="5"/><circle cx="12" cy="78" r="5"/><circle cx="78" cy="78" r="5"/><path d="M17 12h15M73 12H58M17 78h15M73 78H58"/></svg>
  <h3>Microservices</h3><hr>
  <p>Leverage Microservices Architecture to enable quick deployment, dynamically scalable service performance, team productivity and more</p>
</article>
<article class="abs svc" style="left:614px;top:1200px">
  <svg width="90" height="90" viewBox="0 0 90 90" fill="none" stroke="#3fbfb0" stroke-width="2.5"><path d="M20 60a14 14 0 0 1 4-27 18 18 0 0 1 34 4"/><path d="M60 44l14 6v10c0 8-6 13-14 16-8-3-14-8-14-16V50z"/><path d="M54 60l5 5 8-9"/></svg>
  <h3>PLatform engineering</h3><hr>
  <p>For organisations looking to manage the security and cost risks around their cloud infrastructure management for applications</p>
</article>
<article class="abs svc" style="left:853px;top:1246px">
  <svg width="90" height="90" viewBox="0 0 90 90" fill="none" stroke="#3fbfb0" stroke-width="2.5"><rect x="10" y="14" width="50" height="38" rx="4"/><rect x="46" y="36" width="34" height="38" rx="4"/><rect x="26" y="24" width="18" height="18"/></svg>
  <h3>Conversational AI</h3><hr>
  <p>Enabling legacy systems with conversational user interfaces, or simply building intelligent natural language based services, conversational AI has many use cases across sales and operations.</p>
</article>
<div class="abs plus">+</div>
<div class="abs divider"><i></i></div>

<div class="abs news-lines" role="img" aria-label="Curving blue light strands on either side"></div>
<h2 class="abs section-title" style="top:1820px"><span class="b">News</span> <span class="t">&amp; articles</span></h2>
<p class="abs subtitle" style="top:1890px">Updates from our industry</p>

<article class="abs card post" style="top:1994px">
  <h4 style="left:44px;top:30px">AI in SOFTWARE ENGINEERING</h4>
  <p class="lede" style="left:40px;top:78px">10 unexpected ways to use CodePilot</p>
  <p class="ex" style="left:42px;top:118px">(DevHub Blog) CodePilot is widely known for its code generation feature. Learn how the AI assistant's abilities can extend beyond just code generation.</p>
  <div class="thumb" style="left:583px;background:#000" role="img" aria-label="Dark promo graphic with glowing spheres"><div class="thumb-label">CodePilot<br>can do that?!</div></div>
</article>
<article class="abs card post" style="top:2251px">
  <div class="thumb" style="left:21px;background:linear-gradient(120deg,#2a5ae0,#8a5ad0 60%,#e0708a)" role="img" aria-label="Diagram of a starting prompt tree optimized into a simpler tree"><div class="thumb-label" style="align-items:flex-start;padding-top:18px;font-size:17px;font-weight:500">PROMPTA</div></div>
  <h4 style="left:407px;top:32px">INDUSTRY RESEARCH</h4>
  <p class="lede" style="left:404px;top:80px">PROMPTA: A general-purpose framework for prompt optimization</p>
  <p class="ex" style="left:406px;top:118px">(Brightlane Labs) Large language models (LLMs) have revolutionized various tasks, but prompt engineering remains a challenge. Enter PROMPTA: an open-source tool that streamlines prompt optimization, especially for complex structures like Retrieval Augmented Generation (RAG).</p>
</article>
<article class="abs card post" style="top:2508px">
  <h4 style="left:44px;top:30px">BUSINESS INSIGHTS</h4>
  <p class="lede" style="left:40px;top:78px">How Storytelling Helps Data-driven Teams Succeed</p>
  <p class="ex" style="left:42px;top:118px">(DevHub Blog) CodePilot is widely known for its code generation feature. Learn how the AI assistant's abilities can extend beyond just code generation.</p>
  <div class="thumb" style="left:583px;background:linear-gradient(135deg,#1ab8e0,#28d0f0 50%,#b06030)" role="img" aria-label="Basketball dropping through a hoop net against a cyan sky"></div>
</article>
<article class="abs card post" style="top:2765px">
  <div class="thumb" style="left:21px;background:linear-gradient(120deg,#2a5ae0,#8a5ad0 60%,#e0808a)" role="img" aria-label="Icons for medical kit, molecule and chat on a gradient"></div>
  <h4 style="left:407px;top:32px">INDUSTRY RESEARCH</h4>
  <p class="lede" style="left:404px;top:80px">The Power of Prompting</p>
  <p class="ex" style="left:406px;top:118px">(Brightlane Labs) Brightlane discusses Prompting strategies that demonstrates how the generalist Atlas-4 model can perform as a specialist on medical challenge problem benchmarks....</p>
</article>
<div class="abs scroll-track"><i></i></div>

<section>
  <div class="abs news-band" role="img" aria-label="Blue digital circuit dot pattern"></div>
  <h2 class="abs promo">Australia's Largest health charity<br>implements <span class="t">Corvandel API Msg Bus</span></h2>
  <p class="abs subtitle" style="top:3268px;font-size:21px">Register to our newsletter to find out more.</p>
  <form class="abs signup"><div class="field"><svg width="14" height="10" viewBox="0 0 14 10"><rect width="14" height="10" rx="1" fill="#c9d2ea"/></svg>Enter your email</div><div class="go">Subscribe</div></form>
</section>

<section class="abs card consult">
  <span class="o">BOOK</span> an obligation <span class="c">free consultation</span><br>with our <span class="b">Lead Technologist</span>
</section>

<footer>
  <div class="abs brand" style="left:478px;top:3758px"><span class="brand-square"></span>corvandel</div>
  <nav class="abs footer-nav"><a class="active" href="#">Home</a><a href="#">About Us</a><a href="#">Services</a><a href="#">Blog</a><a href="#">Contact Us</a></nav>
  <a class="abs social" style="left:475px;top:3898px">FL</a>
  <a class="abs social" style="left:564px;top:3898px">CL</a>
  <a class="abs social" style="left:653px;top:3898px">WN</a>
  <span class="abs version">M1</span>
</footer>

</body>
</html>
```